Website with a rustic Patriotic Feel

I am looking to design the
Home page I have a mock-up that has the essentials on it like our video, a small slideshow, our plans, and a coverage map, and a small sign up box to be sent a free SIM card.

Eligibility Page: Cool Background with a fill in box that lets the user know if their number is GSM or unlocked.

View Plans page: will have our plans hopefully in their colors with a cool background a walkthrough on Activation.

Activation: If you order your plan first then we send the SIM Card Basically another fill out sheet first name last name ICCID IMEI phone number email

, Contact Us: This is our Customer support page.

Steady Beacon ( this will be our About us page and will have a calendar of Community Volunteer Opportunities.. Right now I have a hodgepodge of different themes that I am going with for the web design. I would like it cohesive with the theme so all of it can fit together nicely.

At the Site map at the bottom we are looking for the basic Menu redirects. quick links to our T&Cs Customer Support and Follow US Buttons as well as a sign up for our Newsletter fill in.

Feel free to redo any of the ads. We are an MVNO like (Northpine Wireless) we provide network Voice and Data Plans our target audience is first Responders and Military. If you are wondering what that green map is its a coverage map to see where to best have coverage. Right now I have a website that uses CMS and HTML. If you are interested in doing a full redesign of our website we would love it.

Right now our website is www.tallow-linkwave.example if you need any additional information.

Target Market(s)

First Responders and Military

Coding

Coded - Design and coding required

Number of Pages Required

5+ page

Font styles to use
Sans Serif

Colors
0455a3
0493ce
f0474d
ffffff

Requirements
Must have
• Cohesive and have a powerpoint and coverage map
Should not have
• Anything flowery or kiddish

```html
<!DOCTYPE html>
<html lang="en">
<head>
<meta charset="utf-8">
<title>Keystone Signal Mobile Services – Home</title>
<link rel="stylesheet" href="https://fonts.googleapis.com/css2?family=Raleway:wght@400;500;600&family=Roboto:wght@400;500;700;900&family=Tinos&display=swap">
<style>
:root{
  --navy:#1f2336;
  --navy-deep:#18233f;
  --blue:#0455a3;
  --sky:#0493ce;
  --red:#f0474d;
  --white:#ffffff;
  --paper:#eef0f3;
  --ink:#222;
  --muted:#666;
  --offer:#1f45d6;
  --green:#3cb34a;
}
*{box-sizing:border-box;margin:0;padding:0}
html,body{width:868px;height:1200px;overflow:hidden}
body{background:#e6e6e6;font-family:"Raleway",sans-serif;color:var(--ink);position:relative}
.page{position:absolute;top:15px;width:778px;height:2200px;transform:scale(.5293);transform-origin:0 0;background:var(--paper);overflow:hidden}
.page--a{left:13px}.page--b{left:435px}
.abs{position:absolute}

/* header */
.site-header{left:0;top:0;width:778px;height:50px;background:var(--navy)}
.brand{left:72px;top:9px;display:flex;align-items:center;gap:6px;color:#3a7ddb;font:700 17px/1 "Roboto",sans-serif;letter-spacing:.5px}
.brand-dot{width:22px;height:22px;border-radius:50%;background:#3a7ddb}
.nav{right:72px;top:19px;display:flex;gap:8px;font:500 10.5px "Roboto",sans-serif;color:var(--white)}
.nav .current{color:var(--red)}
.nav .sep{color:#aaa}

/* hero */
.hero{left:0;top:50px;width:778px;height:235px;background:linear-gradient(100deg,#b5c4d6 0%,#dfe6ee 35%,#c6d3df 65%,#8fa6bd 100%)}
.slide-arrow{top:159px;width:22px;height:22px;border-radius:50%;background:var(--white);border:1px solid #999;display:flex;align-items:center;justify-content:center}
.slide-arrow svg{width:9px;height:9px}

/* info bar */
.info-bar{left:0;top:285px;width:778px;height:63px;background:var(--navy);display:flex;justify-content:center;align-items:center;gap:0;color:var(--white);font:9px/1.7 "Tinos",serif}
.info{display:flex;align-items:center;gap:8px;padding:0 14px;border-right:1px solid #4a4f66}
.info:last-child{border-right:0}
.info svg{width:26px;height:22px;stroke:#ddd;fill:none;stroke-width:1.5}

/* welcome */
.welcome-label{left:0;width:778px;top:402px;text-align:center;color:var(--sky);font:500 11px "Raleway",sans-serif}
.welcome-title{left:0;width:778px;top:415px;text-align:center;font:700 23px "Roboto",sans-serif;color:#111}
.welcome-text{left:80px;width:618px;top:452px;text-align:center;font:9px/18px "Raleway",sans-serif;color:var(--muted)}
.promo{left:72px;top:524px;width:310px;height:186px;background:linear-gradient(135deg,#dde8f5,#f3e8f0 60%,#c9d8ee);box-shadow:0 3px 8px rgba(0,0,0,.3)}
.video{left:395px;top:524px;width:310px;height:186px;background:linear-gradient(160deg,#232a3d,#0e1220);box-shadow:0 3px 8px rgba(0,0,0,.3)}
.play{left:140px;top:72px;width:30px;height:30px;border-radius:50%;background:var(--white);display:flex;align-items:center;justify-content:center}
.video-bar{left:0;bottom:0;width:310px;height:18px;background:rgba(0,0,0,.6)}

/* offer */
.offer{left:0;top:765px;width:778px;height:205px;background:var(--offer)}
.offer-flags{right:0;top:0;width:240px;height:205px;background:linear-gradient(120deg,rgba(31,69,214,0),#c9424a 40%,#e8e8f0 60%,#2a3c8f)}
.offer-text{left:120px;width:520px;top:55px;text-align:center;color:var(--white);font-family:"Roboto",sans-serif;font-weight:900;line-height:1}
.offer-text .l1{font-size:25px;letter-spacing:.5px}
.offer-text .l2{font-size:16px;margin-top:4px}
.offer-text .l3{font-size:24px}
.offer-text .l4{font-size:16px;margin-top:2px}

/* sections titles */
.section-title{left:0;width:778px;text-align:center;font:400 25px "Roboto",sans-serif;color:#111}
.section-rule{left:373px;width:32px;height:3px;background:var(--red)}

/* plans */
.plan{background:var(--white);box-shadow:0 2px 6px rgba(0,0,0,.12);text-align:center}
.plan-head{color:var(--white);font:500 11px "Roboto",sans-serif;display:flex;align-items:flex-end;justify-content:center;padding-bottom:8px;position:relative}
.plan-head::before{content:"";position:absolute;top:9px;left:50%;width:18px;height:2px;margin-left:-9px;background:var(--white)}
.plan-from{font:500 6px "Raleway",sans-serif;color:#444;margin-top:14px;text-transform:uppercase}
.plan-price{font:500 19px "Roboto",sans-serif;color:var(--blue)}
.plan-per{font:6px "Raleway",sans-serif;color:#444;margin-bottom:8px}
.plan-list{list-style:none;text-align:left;padding-left:34px;font:500 8px "Raleway",sans-serif;color:#333}
.plan-list li{line-height:18px;display:flex;align-items:center;gap:4px}
.plan-list li::before{content:"";width:7px;height:7px;border-radius:50%;background:var(--red);flex:none}
.plan--gold .plan-list{font-size:10.5px;padding-left:42px}
.plan--gold .plan-list li{line-height:22px}
.plan--gold .plan-price{font-size:23px}
.plan--gold .plan-from,.plan--gold .plan-per{font-size:7.5px}
.subscribe-btn{left:335px;top:1309px;width:108px;height:34px;border-radius:17px;background:#e8b931;color:var(--white);font:500 12px "Roboto",sans-serif;display:flex;align-items:center;justify-content:center;box-shadow:0 2px 4px rgba(0,0,0,.2)}

/* coverage */
.coverage-panel{left:65px;top:1457px;width:320px;height:238px;background:var(--white);box-shadow:0 1px 4px rgba(0,0,0,.15)}
.tabs{left:3px;top:3px;display:flex;gap:3px}
.tab{height:24px;padding:0 10px;display:flex;align-items:center;font:500 9px "Roboto",sans-serif;color:var(--white);background:var(--blue)}
.tab--active{background:var(--white);color:var(--blue);border:1px solid var(--blue)}
.loc-box{left:5px;top:40px;width:308px;height:100px;border-top:1px solid #e2e2e2;border-bottom:1px solid #e2e2e2}
.loc-title{left:10px;top:13px;font:500 12px "Roboto",sans-serif;display:flex;gap:4px;align-items:center}
.my-route{right:10px;top:14px;font:500 9.5px "Raleway",sans-serif;color:var(--blue)}
.loc-input{left:10px;top:35px;width:290px;height:28px;border:1px solid #ccc;display:flex;align-items:center;padding-left:10px;font:8px "Raleway",sans-serif;color:#888}
.loc-search{right:-1px;top:-1px;width:28px;height:28px;background:var(--blue);display:flex;align-items:center;justify-content:center}
.loc-current{left:0;width:308px;top:77px;text-align:center;font:500 9.5px "Raleway",sans-serif;color:var(--blue)}
.legend{left:14px;font:500 10.5px "Raleway",sans-serif;color:#444}
.legend-dot{left:297px;width:11px;height:11px;border-radius:50%}
.legend-foot{top:213px;font:500 11px "Raleway",sans-serif;color:var(--blue)}
.map{left:393px;top:1457px;width:320px;height:238px;background:linear-gradient(160deg,#a9c3e6 0%,#2d69b5 40%,#1d5aa8 65%,#b9cfec 100%)}

/* subscribe */
.subscribe{left:0;top:1750px;width:778px;height:210px;background:linear-gradient(180deg,#2b3b5e,#3a5173 55%,#20304f)}
.subscribe-title{left:0;width:778px;top:1800px;text-align:center;color:var(--white);font:400 23px "Roboto",sans-serif}
.subscribe-sub{left:0;width:778px;top:1845px;text-align:center;color:var(--white);font:500 11px "Raleway",sans-serif}
.email{left:210px;top:1872px;width:250px;height:32px;border-radius:16px;background:var(--white);font:8.5px "Raleway",sans-serif;color:#888;display:flex;align-items:center;padding-left:14px}
.email-btn{left:464px;top:1872px;width:105px;height:32px;border-radius:16px;background:#1f7fd0;color:var(--white);font:500 10px "Roboto",sans-serif;display:flex;align-items:center;justify-content:center}

/* footer */
.footer{left:0;top:1960px;width:778px;height:240px;background:#eceef1}
.f-col{top:2008px;font:9px/18.5px "Raleway",sans-serif;color:#777}
.f-col h4{font:500 10px "Roboto",sans-serif;color:#222;margin-bottom:3px;letter-spacing:.3px}
.social{display:flex;gap:5px;margin-top:5px}
.social span{width:7px;height:7px;border-radius:50%;background:#888}
.chat{left:636px;top:2108px;width:72px;height:25px;border-radius:13px;background:var(--green);color:var(--white);font:500 9px "Roboto",sans-serif;display:flex;align-items:center;justify-content:center}
.copyright{left:72px;top:2157px;font:9px "Raleway",sans-serif;color:#555}
.cards{left:420px;top:2147px;width:285px;display:flex;flex-wrap:wrap;justify-content:flex-end;gap:8px 7px}
.cards span{width:25px;height:15px;border-radius:2px;background:#fff;border:1px solid #bbb}
.cards span.dark{background:#2d6fc4;border-color:#2d6fc4}
</style>
</head>
<body>

<main class="page page--a">
  <header class="abs site-header">
    <div class="abs brand"><span class="brand-dot"></span>KEYSTONE SIGNAL</div>
    <nav class="abs nav"><span class="current">Home</span><span class="sep">|</span><span>View Plans</span><span class="sep">|</span><span>Activate Today</span><span class="sep">|</span><span>Contact Us</span><span class="sep">|</span><span>Steady Beacon</span><span class="sep">|</span><span>My Account</span></nav>
  </header>
  <div class="abs hero" role="img" aria-label="Hero slide: flag, first responders, navy ship, helicopter and jet with Keystone Signal Mobile Services title"></div>
  <div class="abs slide-arrow" style="left:22px"><svg viewBox="0 0 10 10"><path d="M7 1 3 5l4 4" stroke="#333" fill="none" stroke-width="1.5"/></svg></div>
  <div class="abs slide-arrow" style="right:22px"><svg viewBox="0 0 10 10"><path d="M3 1l4 4-4 4" stroke="#333" fill="none" stroke-width="1.5"/></svg></div>
  <section class="abs info-bar">
    <div class="info"><svg viewBox="0 0 26 22"><rect x="2" y="5" width="14" height="11"/><path d="M16 9h5l3 4v3h-8"/><circle cx="7" cy="18" r="2"/><circle cx="20" cy="18" r="2"/></svg><div>Great Prices on Our Lines<br>Free Shipping for SIM Cards</div></div>
    <div class="info"><svg viewBox="0 0 26 22"><rect x="8" y="1" width="10" height="20" rx="2"/><path d="M11 18h4"/></svg><div>Give Us A Call<br>+1(833)555-0148</div></div>
    <div class="info"><svg viewBox="0 0 26 22"><ellipse cx="11" cy="10" rx="9" ry="7"/><path d="M8 8h7M8 11h5M20 7c3 1 5 3 5 6"/></svg><div>Chat With US<br>WE offer 24-hour chat support</div></div>
    <div class="info"><svg viewBox="0 0 26 22"><path d="M2 8h22v12H2zM2 8l3-6h16l3 6"/><path d="M10 20v-6h6v6"/></svg><div>Nationwide Coverage<br>4G LTE High Speed Data</div></div>
  </section>

  <div class="abs welcome-label">Welcome To</div>
  <h1 class="abs welcome-title">KEYSTONE SIGNAL</h1>
  <p class="abs welcome-text">Lorem ipsum dolor sit amet, consectetur adipiscing elit, sed do eiusmod tempor incididunt ut labore et dolore magna aliqua. Quis ipsum suspendisse ultrices gravida. Risus commodo viverra maecenas accumsan lacus vel facilisis. Lorem ipsum dolor sit amet, consectetur adipiscing elit, sed do eiusmod tempor incididunt ut labore et dolore magna aliqua.</p>
  <div class="abs promo" role="img" aria-label="Promo slide: plan tier bar chart with family plan and data plan offers"></div>
  <div class="abs video" role="img" aria-label="Company video">
    <div class="abs play"><svg width="12" height="12" viewBox="0 0 12 12"><path d="M3 1l8 5-8 5z" fill="#d8262d"/></svg></div>
    <div class="abs video-bar"></div>
  </div>

  <section class="abs offer">
    <div class="abs offer-flags" role="img" aria-label="Waving American flags"></div>
    <div class="abs offer-text">
      <div class="l1">LIMITED-TIME OFFER!</div>
      <div class="l2">Military and first responders will recieve their first</div>
      <div class="l3">2 DECEMBERS FOR FREE</div>
      <div class="l4">with a two year contract.</div>
    </div>
  </section>

  <h2 class="abs section-title" style="top:1020px">CHOOSE PRICING PLAN</h2>
  <div class="abs section-rule" style="top:1055px"></div>

  <div class="abs plan" style="left:80px;top:1100px;width:107px;height:205px">
    <div class="plan-head" style="height:38px;background:linear-gradient(#c9ad85,#b8986b)">BRONZE</div>
    <div class="plan-from">Starting From</div><div class="plan-price">$20.00</div><div class="plan-per">PER MONTH</div>
    <ul class="plan-list" style="padding-left:14px"><li>Data &amp; Voice</li><li>Unlimited Talk</li><li>Unlimited Text</li><li>100MB</li><li>4G LTE DATA</li></ul>
  </div>
  <div class="abs plan" style="left:187px;top:1093px;width:115px;height:215px">
    <div class="plan-head" style="height:38px;background:linear-gradient(#f2f2f2,#d8d8d8);color:#333">SILVER</div>
    <div class="plan-from">Starting From</div><div class="plan-price">$25.00</div><div class="plan-per">PER MONTH</div>
    <ul class="plan-list" style="padding-left:14px"><li>Data &amp; Voice</li><li>Unlimited Talk</li><li>Unlimited Text</li><li>1GB</li><li>4G LTE DATA</li></ul>
  </div>
  <div class="abs plan plan--gold" style="left:302px;top:1073px;width:176px;height:258px">
    <div class="plan-head" style="height:48px;background:linear-gradient(#edc23b,#e0ad23)">GOLD</div>
    <div class="plan-from">Starting From</div><div class="plan-price">$35.00</div><div class="plan-per">PER MONTH</div>
    <ul class="plan-list"><li>Data &amp; Voice</li><li>Unlimited Talk</li><li>Unlimited Text</li><li>3GB</li><li>4G LTE DATA</li></ul>
  </div>
  <div class="abs plan" style="left:478px;top:1093px;width:115px;height:215px">
    <div class="plan-head" style="height:38px;background:linear-gradient(#5b5653,#3a3634)">PLATINUM</div>
    <div class="plan-from">Starting From</div><div class="plan-price">$50.00</div><div class="plan-per">PER MONTH</div>
    <ul class="plan-list" style="padding-left:14px"><li>Data &amp; Voice</li><li>Unlimited Talk</li><li>Unlimited Text</li><li>100MB</li><li>4G LTE DATA</li></ul>
  </div>
  <div class="abs plan" style="left:593px;top:1100px;width:107px;height:205px">
    <div class="plan-head" style="height:38px;background:linear-gradient(#2b91d4,#1870b3)">DIAMOND</div>
    <div class="plan-from">Starting From</div><div class="plan-price">$65.00</div><div class="plan-per">PER MONTH</div>
    <ul class="plan-list" style="padding-left:12px"><li>Data &amp; Voice</li><li>Unlimited Talk</li><li>Unlimited Text</li><li>Unlimited Data</li><li>Upto 22 GB</li></ul>
  </div>
  <div class="abs subscribe-btn">SUBSCRIBE</div>

  <h2 class="abs section-title" style="top:1398px">OUR COVERAGE AREAS</h2>
  <div class="abs section-rule" style="top:1433px"></div>
  <div class="abs coverage-panel">
    <div class="abs tabs"><span class="tab tab--active" style="width:72px;justify-content:center">Wireless</span><span class="tab">Meridian PREPAID</span><span class="tab">International</span><span class="tab">Meridian Stores</span></div>
    <div class="abs loc-box">
      <div class="abs loc-title"><svg width="11" height="13" viewBox="0 0 11 13"><path d="M5.5 12S1 7 1 4.5a4.5 4.5 0 0 1 9 0C10 7 5.5 12 5.5 12z" fill="none" stroke="#e03a3f" stroke-width="1.3"/><circle cx="5.5" cy="4.5" r="1.5" fill="#e03a3f"/></svg>Location</div>
      <div class="abs my-route">My Route</div>
      <div class="abs loc-input">Enter address,state or zip code<div class="abs loc-search"><svg width="11" height="11" viewBox="0 0 11 11"><circle cx="4.5" cy="4.5" r="3.3" fill="none" stroke="#fff" stroke-width="1.5"/><path d="M7 7l3 3" stroke="#fff" stroke-width="1.5"/></svg></div></div>
      <div class="abs loc-current">&#9679; Use my current location</div>
    </div>
    <div class="abs legend" style="top:170px">Coverage</div>
    <div class="abs legend-dot" style="top:173px;background:#e8463f;box-shadow:0 0 0 2px #1f7fd0 inset"></div>
    <div class="abs legend" style="top:192px">No Coverage</div>
    <div class="abs legend-dot" style="top:195px;background:#1f7fd0"></div>
    <div class="abs legend-foot" style="left:14px">Available 5G Cities</div>
    <div class="abs legend-foot" style="left:150px">Learn more about the legend</div>
  </div>
  <div class="abs map" role="img" aria-label="Coverage map of North America with covered areas in blue"></div>

  <section class="abs subscribe" role="img" aria-label="American flag waving against a cloudy sky"></section>
  <h2 class="abs subscribe-title">SUBSCRIBE TODAY</h2>
  <p class="abs subscribe-sub">Get The Latest News On Discounts &amp; Offers</p>
  <div class="abs email">Enter your email</div>
  <div class="abs email-btn">SUBSCRIBE</div>

  <footer class="abs footer"></footer>
  <div class="abs f-col" style="left:72px"><h4>MAIN MENU</h4>Home<br>Catalog<br>View Plans<br>Activate Today<br>Contact Us<br>Steady Beacon</div>
  <div class="abs f-col" style="left:241px"><h4>QUICK LINKS</h4>Terms &amp; Conditions<br>Activating Your Service<br>Acceptable Use Policy<br>Wireless Privacy Policy<br>Coverage Map</div>
  <div class="abs f-col" style="left:441px"><h4>CUSTOMER SUPPORT</h4>View Plans<br>Contact Us<br>Phone: +1(833)555-0148</div>
  <div class="abs f-col" style="left:647px"><h4>FOLLOW US</h4><div class="social"><span></span><span></span><span></span></div></div>
  <div class="abs chat">LIVE CHAT</div>
  <div class="abs copyright">Copyright © 2020 Keystone Signal All Rights Reserved</div>
  <div class="abs cards"><span class="dark"></span><span></span><span></span><span></span><span></span><span></span><span></span><span></span><span class="dark"></span><span class="dark"></span><span></span></div>
</main>

<main class="page page--b">
  <header class="abs site-header">
    <div class="abs brand"><span class="brand-dot"></span>KEYSTONE SIGNAL</div>
    <nav class="abs nav"><span class="current">Home</span><span class="sep">|</span><span>View Plans</span><span class="sep">|</span><span>Activate Today</span><span class="sep">|</span><span>Contact Us</span><span class="sep">|</span><span>Steady Beacon</span><span class="sep">|</span><span>My Account</span></nav>
  </header>
  <div class="abs hero" role="img" aria-label="Hero slide: flag, first responders, navy ship, helicopter and jet with Keystone Signal Mobile Services title"></div>
  <div class="abs slide-arrow" style="left:22px"><svg viewBox="0 0 10 10"><path d="M7 1 3 5l4 4" stroke="#333" fill="none" stroke-width="1.5"/></svg></div>
  <div class="abs slide-arrow" style="right:22px"><svg viewBox="0 0 10 10"><path d="M3 1l4 4-4 4" stroke="#333" fill="none" stroke-width="1.5"/></svg></div>
  <section class="abs info-bar">
    <div class="info"><svg viewBox="0 0 26 22"><rect x="2" y="5" width="14" height="11"/><path d="M16 9h5l3 4v3h-8"/><circle cx="7" cy="18" r="2"/><circle cx="20" cy="18" r="2"/></svg><div>Great Prices on Our Lines<br>Free Shipping for SIM Cards</div></div>
    <div class="info"><svg viewBox="0 0 26 22"><rect x="8" y="1" width="10" height="20" rx="2"/><path d="M11 18h4"/></svg><div>Give Us A Call<br>+1(833)555-0148</div></div>
    <div class="info"><svg viewBox="0 0 26 22"><ellipse cx="11" cy="10" rx="9" ry="7"/><path d="M8 8h7M8 11h5M20 7c3 1 5 3 5 6"/></svg><div>Chat With US<br>WE offer 24-hour chat support</div></div>
    <div class="info"><svg viewBox="0 0 26 22"><path d="M2 8h22v12H2zM2 8l3-6h16l3 6"/><path d="M10 20v-6h6v6"/></svg><div>Nationwide Coverage<br>4G LTE High Speed Data</div></div>
  </section>

  <div class="abs welcome-label">Welcome To</div>
  <h1 class="abs welcome-title">KEYSTONE SIGNAL</h1>
  <p class="abs welcome-text">Lorem ipsum dolor sit amet, consectetur adipiscing elit, sed do eiusmod tempor incididunt ut labore et dolore magna aliqua. Quis ipsum suspendisse ultrices gravida. Risus commodo viverra maecenas accumsan lacus vel facilisis. Lorem ipsum dolor sit amet, consectetur adipiscing elit, sed do eiusmod tempor incididunt ut labore et dolore magna aliqua.</p>
  <div class="abs promo" role="img" aria-label="Promo slide: plan tier bar chart with family plan and data plan offers"></div>
  <div class="abs video" role="img" aria-label="Company video">
    <div class="abs play"><svg width="12" height="12" viewBox="0 0 12 12"><path d="M3 1l8 5-8 5z" fill="#d8262d"/></svg></div>
    <div class="abs video-bar"></div>
  </div>

  <section class="abs offer">
    <div class="abs offer-flags" role="img" aria-label="Waving American flags"></div>
    <div class="abs offer-text">
      <div class="l1">LIMITED-TIME OFFER!</div>
      <div class="l2">Military and first responders will recieve their first</div>
      <div class="l3">2 DECEMBERS FOR FREE</div>
      <div class="l4">with a two year contract.</div>
    </div>
  </section>

  <h2 class="abs section-title" style="top:1020px">CHOOSE PRICING PLAN</h2>
  <div class="abs section-rule" style="top:1055px"></div>

  <div class="abs plan" style="left:80px;top:1100px;width:107px;height:205px">
    <div class="plan-head" style="height:38px;background:linear-gradient(#c9ad85,#b8986b)">BRONZE</div>
    <div class="plan-from">Starting From</div><div class="plan-price">$20.00</div><div class="plan-per">PER MONTH</div>
    <ul class="plan-list" style="padding-left:14px"><li>Data &amp; Voice</li><li>Unlimited Talk</li><li>Unlimited Text</li><li>100MB</li><li>4G LTE DATA</li></ul>
  </div>
  <div class="abs plan" style="left:187px;top:1093px;width:115px;height:215px">
    <div class="plan-head" style="height:38px;background:linear-gradient(#f2f2f2,#d8d8d8);color:#333">SILVER</div>
    <div class="plan-from">Starting From</div><div class="plan-price">$25.00</div><div class="plan-per">PER MONTH</div>
    <ul class="plan-list" style="padding-left:14px"><li>Data &amp; Voice</li><li>Unlimited Talk</li><li>Unlimited Text</li><li>1GB</li><li>4G LTE DATA</li></ul>
  </div>
  <div class="abs plan plan--gold" style="left:302px;top:1073px;width:176px;height:258px">
    <div class="plan-head" style="height:48px;background:linear-gradient(#edc23b,#e0ad23)">GOLD</div>
    <div class="plan-from">Starting From</div><div class="plan-price">$35.00</div><div class="plan-per">PER MONTH</div>
    <ul class="plan-list"><li>Data &amp; Voice</li><li>Unlimited Talk</li><li>Unlimited Text</li><li>3GB</li><li>4G LTE DATA</li></ul>
  </div>
  <div class="abs plan" style="left:478px;top:1093px;width:115px;height:215px">
    <div class="plan-head" style="height:38px;background:linear-gradient(#5b5653,#3a3634)">PLATINUM</div>
    <div class="plan-from">Starting From</div><div class="plan-price">$50.00</div><div class="plan-per">PER MONTH</div>
    <ul class="plan-list" style="padding-left:14px"><li>Data &amp; Voice</li><li>Unlimited Talk</li><li>Unlimited Text</li><li>100MB</li><li>4G LTE DATA</li></ul>
  </div>
  <div class="abs plan" style="left:593px;top:1100px;width:107px;height:205px">
    <div class="plan-head" style="height:38px;background:linear-gradient(#2b91d4,#1870b3)">DIAMOND</div>
    <div class="plan-from">Starting From</div><div class="plan-price">$65.00</div><div class="plan-per">PER MONTH</div>
    <ul class="plan-list" style="padding-left:12px"><li>Data &amp; Voice</li><li>Unlimited Talk</li><li>Unlimited Text</li><li>Unlimited Data</li><li>Upto 22 GB</li></ul>
  </div>
  <div class="abs subscribe-btn">SUBSCRIBE</div>

  <h2 class="abs section-title" style="top:1398px">OUR COVERAGE AREAS</h2>
  <div class="abs section-rule" style="top:1433px"></div>
  <div class="abs coverage-panel">
    <div class="abs tabs"><span class="tab tab--active" style="width:72px;justify-content:center">Wireless</span><span class="tab">Meridian PREPAID</span><span class="tab">International</span><span class="tab">Meridian Stores</span></div>
    <div class="abs loc-box">
      <div class="abs loc-title"><svg width="11" height="13" viewBox="0 0 11 13"><path d="M5.5 12S1 7 1 4.5a4.5 4.5 0 0 1 9 0C10 7 5.5 12 5.5 12z" fill="none" stroke="#e03a3f" stroke-width="1.3"/><circle cx="5.5" cy="4.5" r="1.5" fill="#e03a3f"/></svg>Location</div>
      <div class="abs my-route">My Route</div>
      <div class="abs loc-input">Enter address,state or zip code<div class="abs loc-search"><svg width="11" height="11" viewBox="0 0 11 11"><circle cx="4.5" cy="4.5" r="3.3" fill="none" stroke="#fff" stroke-width="1.5"/><path d="M7 7l3 3" stroke="#fff" stroke-width="1.5"/></svg></div></div>
      <div class="abs loc-current">&#9679; Use my current location</div>
    </div>
    <div class="abs legend" style="top:170px">Coverage</div>
    <div class="abs legend-dot" style="top:173px;background:#e8463f;box-shadow:0 0 0 2px #1f7fd0 inset"></div>
    <div class="abs legend" style="top:192px">No Coverage</div>
    <div class="abs legend-dot" style="top:195px;background:#1f7fd0"></div>
    <div class="abs legend-foot" style="left:14px">Available 5G Cities</div>
    <div class="abs legend-foot" style="left:150px">Learn more about the legend</div>
  </div>
  <div class="abs map" role="img" aria-label="Coverage map of North America with covered areas in blue"></div>

  <section class="abs subscribe" role="img" aria-label="American flag waving against a cloudy sky"></section>
  <h2 class="abs subscribe-title">SUBSCRIBE TODAY</h2>
  <p class="abs subscribe-sub">Get The Latest News On Discounts &amp; Offers</p>
  <div class="abs email">Enter your email</div>
  <div class="abs email-btn">SUBSCRIBE</div>

  <footer class="abs footer"></footer>
  <div class="abs f-col" style="left:72px"><h4>MAIN MENU</h4>Home<br>Catalog<br>View Plans<br>Activate Today<br>Contact Us<br>Steady Beacon</div>
  <div class="abs f-col" style="left:241px"><h4>QUICK LINKS</h4>Terms &amp; Conditions<br>Activating Your Service<br>Acceptable Use Policy<br>Wireless Privacy Policy<br>Coverage Map</div>
  <div class="abs f-col" style="left:441px"><h4>CUSTOMER SUPPORT</h4>View Plans<br>Contact Us<br>Phone: +1(833)555-0148</div>
  <div class="abs f-col" style="left:647px"><h4>FOLLOW US</h4><div class="social"><span></span><span></span><span></span></div></div>
  <div class="abs chat">LIVE CHAT</div>
  <div class="abs copyright">Copyright © 2020 Keystone Signal All Rights Reserved</div>
  <div class="abs cards"><span class="dark"></span><span></span><span></span><span></span><span></span><span></span><span></span><span></span><span class="dark"></span><span class="dark"></span><span></span></div>
</main>

</body>
</html>
```